Bramblewood Joinery Website

My client Bramblewood Joinery is looking for a redesign for a Word Press Website. Their current site is at www.bramblewoodjoinery.example They are a custom cabinet company, but also create bathroom, living room, bar and entertainment and bedroom cabinets too. They would like a design that emulates the master craftsman work they do yet a contemporary style.

Their current site was designed using Flash elements.

Target Market(s)

Home owners and builders of high end homes

Industry/Entity Type

Entertainment

Font styles to use
Serif
Decorative

Requirements
Must have
• Must show their work and logo using a contemporary style.
Nice to have
• Sliders that showcase their projects.

```html
<!DOCTYPE html>
<html lang="en">
<head>
<meta charset="utf-8">
<title>Bramblewood Joinery</title>
<link href="https://fonts.googleapis.com/css2?family=Poiret+One&family=PT+Sans:wght@400;700&family=Maven+Pro:wght@500;600&family=Cabin:wght@400;600&display=swap" rel="stylesheet">
<style>
:root{
  --green:#2f9e34;
  --green-light:#43b547;
  --green-text:#2ea82f;
  --dark:#1c1c1c;
  --darker:#151515;
  --ink:#222;
  --body:#444;
  --muted:#aaa;
  --rule:#ddd;
}
*{margin:0;padding:0;box-sizing:border-box}
html,body{width:1088px;height:1200px;overflow:hidden;background:#fff}
.page{position:relative;width:1200px;height:1324px;transform:scale(.9067);transform-origin:0 0;font-family:"Cabin",sans-serif;color:var(--body)}
.abs{position:absolute}
.header{left:0;top:0;width:1200px;height:107px;background:linear-gradient(#fff,#ececec)}
.brand{left:118px;top:8px;display:flex;align-items:center;gap:14px}
.brand-dot{width:90px;height:90px;border-radius:50%;background:var(--green)}
.brand-name{font-family:"Poiret One",sans-serif;font-size:25px;line-height:30px;color:var(--ink);font-weight:400}
.account{right:112px;top:13px;font-family:"PT Sans",sans-serif;font-size:13px;color:#333}
.account b{color:var(--green-text)}
.callus{right:110px;top:31px;font-family:"PT Sans",sans-serif;font-size:23px;color:var(--ink)}
.callus span{color:var(--green-light)}
.search{left:845px;top:66px;width:204px;height:26px;border:1px solid #ddd;background:#fff;font-size:13px;color:#bbb;padding:5px 0 0 26px}
.search svg{position:absolute;left:8px;top:6px}
.search-btn{left:1055px;top:66px;width:34px;height:27px;background:var(--green-light)}
.nav{left:0;top:107px;width:1200px;height:44px;background:linear-gradient(#2b2b2b,#141414);display:flex;justify-content:center}
.nav ul{display:flex;list-style:none;margin-left:-10px;border-left:1px solid #3a3a3a}
.nav li{font-family:"PT Sans",sans-serif;font-size:15px;color:#eee;line-height:44px;padding:0 19px;border-right:1px solid #3a3a3a}
.hero{left:0;top:151px;width:1200px;height:377px;background:linear-gradient(135deg,#3aa53e,#2a8f2f 60%,#3aa73f)}
.hero-title{left:110px;top:192px;width:330px;font-family:"Poiret One",sans-serif;font-size:44px;line-height:46px;color:#fff;font-weight:400}
.hero-text{left:111px;top:342px;width:320px;font-size:15px;line-height:22.5px;color:#fff}
.btn-dark{left:111px;top:425px;width:122px;height:40px;background:#1b1b1b;color:#fff;font-size:14.5px;text-align:center;line-height:40px}
.hero-photo{left:453px;top:198px;width:637px;height:250px;border:5px solid #e6e6e6;background:linear-gradient(#c9b9a2,#e8e4de 45%,#8a5a3a 85%,#5b3620)}
.carousel{left:110px;top:493px;width:982px;height:132px;background:linear-gradient(#f6f6f6,#e3e3e3);box-shadow:0 6px 6px -4px rgba(0,0,0,.2)}
.arrow{top:541px;width:38px;height:38px;border-radius:50%;background:#3a3a3a}
.thumb{top:522px;width:120px;height:77px;border:4px solid #fff;box-shadow:0 1px 3px rgba(0,0,0,.25)}
.thumb.active{border-color:var(--green-light)}
.col-h{top:660px;font-family:"Maven Pro",sans-serif;font-size:19px;font-weight:500;color:var(--ink);border-left:5px solid var(--green-light);padding-left:8px;line-height:28px;white-space:nowrap}
.col-h span{color:var(--green-light)}
.col-p{font-size:12.5px;line-height:22px;color:var(--body)}
.btn-green{top:917px;width:112px;height:36px;background:linear-gradient(var(--green-light),var(--green));color:#fff;font-size:14.5px;text-align:center;line-height:36px}
.video{left:446px;top:703px;width:312px;height:126px;border:5px solid #eee;background:linear-gradient(90deg,#3a3a3a,#8b8b8b 60%,#5d5d5d)}
.news-date{font-size:11px;color:#333}
.news-link{font-size:12.5px;line-height:20px;color:var(--green-text)}
.footer{left:0;top:986px;width:1200px;height:338px;background:var(--dark)}
.flinks{list-style:none;font-size:12.5px;color:#eee}
.flinks li{line-height:25px}
.fdiv{left:757px;top:1022px;width:1px;height:153px;background:#333}
.office{left:805px;top:1025px;font-size:13px;color:#ddd}
.office b{color:#fff;font-weight:600}
.office p{color:#999;font-size:12px;line-height:17px;margin-top:10px}
.email{left:806px;top:1097px;font-size:13px;color:#fff;font-weight:600;display:flex;gap:6px;align-items:center}
.tollfree{left:803px;top:1133px;width:286px;height:42px;background:#111;color:#fff;font-size:15px;font-weight:600;padding:11px 12px;display:flex;align-items:center;gap:10px}
.band{left:0;width:1200px;height:1px;background:#2c2c2c}
.newsletter{left:113px;top:1222px;font-size:13.5px;color:#fff;font-weight:600;display:flex;gap:9px;align-items:center}
.nl-input{left:300px;top:1219px;width:373px;height:28px;background:#fff}
.nl-go{left:673px;top:1219px;width:40px;height:28px;background:var(--green-light);color:#fff;font-size:13px;font-weight:600;text-align:center;line-height:28px}
.social{top:1222px;width:23px;height:23px}
.copy{top:1286px;font-size:12.5px;color:#aaa}
</style>
</head>
<body>
<div class="page">
  <header class="abs header"></header>
  <div class="abs brand"><div class="brand-dot"></div><div class="brand-name">Kansas City's Premier Custom Kitchen<br>Cabinet Design Company</div></div>
  <div class="abs account"><b>Login</b> &nbsp;|&nbsp; Register</div>
  <div class="abs callus"><span>Call US</span> : 555-014-2290</div>
  <div class="abs search"><svg width="12" height="12" viewBox="0 0 12 12"><circle cx="5" cy="5" r="4" fill="none" stroke="#ccc" stroke-width="1.5"/><line x1="8" y1="8" x2="11" y2="11" stroke="#ccc" stroke-width="1.5"/></svg>Search</div>
  <div class="abs search-btn"><svg width="34" height="27" viewBox="0 0 34 27"><path d="M11 8l5 5.5-5 5.5M17 8l5 5.5-5 5.5" fill="none" stroke="#fff" stroke-width="2.2"/></svg></div>
  <nav class="abs nav"><ul><li>Home</li><li>Who We Are</li><li>Getting Started</li><li>Contact Us</li><li>Customer Experience</li><li>Professional</li><li>Portfolio</li><li>Cabinet Hardware</li></ul></nav>

  <section class="abs hero"></section>
  <h1 class="abs hero-title">Bramblewood<br>Joinery &amp;<br>Fixtures</h1>
  <p class="abs hero-text">Lorem ipsum dolor sit consectetur adipiscing sed do eiusmod tempor aliqua enim is minim nisi ut aliquip ex ea commodo.</p>
  <div class="abs btn-dark">Read More</div>
  <div class="abs hero-photo" role="img" aria-label="Photo of a white shaker kitchen with steel range and wood floor"></div>

  <div class="abs carousel"></div>
  <div class="abs arrow" style="left:132px"><svg width="38" height="38"><path d="M22 12l-7 7 7 7" fill="none" stroke="#fff" stroke-width="3"/></svg></div>
  <div class="abs arrow" style="left:1033px"><svg width="38" height="38"><path d="M16 12l7 7-7 7" fill="none" stroke="#fff" stroke-width="3"/></svg></div>
  <div class="abs thumb" style="left:180px;background:linear-gradient(#a06a3e,#6b4024)" role="img" aria-label="Walk-in closet cabinetry"></div>
  <div class="abs thumb" style="left:325px;background:linear-gradient(#b0733a,#6a3b1c)" role="img" aria-label="Warm wood kitchen"></div>
  <div class="abs thumb" style="left:469px;background:linear-gradient(#ddd,#9a9a9a)" role="img" aria-label="Modern grey kitchen"></div>
  <div class="abs thumb" style="left:614px;background:linear-gradient(#e2ddd2,#8b7863)" role="img" aria-label="White kitchen with island"></div>
  <div class="abs thumb active" style="left:758px;background:linear-gradient(#cfc3b0,#eee 50%,#6e4a30)" role="img" aria-label="White shaker kitchen"></div>
  <div class="abs thumb" style="left:903px;background:linear-gradient(#8a5328,#4a2a14)" role="img" aria-label="Dark wood kitchen"></div>

  <h2 class="abs col-h" style="left:110px">WELCOME TO <span>BRAMBLEWOOD</span></h2>
  <p class="abs col-p" style="left:110px;top:699px;width:305px">Established in 1966, Bramblewood Joinery has long stood as one of the Midwest's most renowned makers of custom cabinets and fixtures. Our handcrafted, award-winning creations have been chosen by hundreds of noteworthy homebuilders. And while we custom build cabinets, we built our business around the belief that our customers absolutely, unequivocally come first. From day one, our mission has been to help turn the houses that people live in to the homes they've always...</p>
  <div class="abs btn-green" style="left:110px">Read More</div>

  <h2 class="abs col-h" style="left:446px">OUR <span>VIDEO</span></h2>
  <div class="abs video" role="img" aria-label="Video still of a dark modern kitchen"><svg class="abs" style="left:125px;top:33px" width="52" height="52"><circle cx="26" cy="26" r="23" fill="rgba(0,0,0,.3)" stroke="#fff" stroke-width="4"/><path d="M20 16l15 10-15 10z" fill="#fff"/></svg></div>
  <p class="abs col-p" style="left:446px;top:835px;width:315px">At Bramblewood Joinery, we've been designing and manu-facturing the Midwest's finest custom cabinets and fixtures since 1966. From single cabinets to room remodels to</p>
  <div class="abs btn-green" style="left:445px">Read More</div>

  <h2 class="abs col-h" style="left:790px">LATEST <span>NEWS</span></h2>
  <div class="abs" style="left:789px;top:703px;width:302px">
    <div class="news-date">&raquo; 17 JAN 2015</div>
    <p class="news-link" style="margin-top:3px">Lorem ipsum dolor sit amet, consectetur adipiscing elit, sed do eiusmod tempor incididunt ut labore.</p>
    <div style="height:1px;background:var(--rule);margin:8px 0 13px"></div>
    <div class="news-date">&raquo; 17 JAN 2015</div>
    <p class="news-link" style="margin-top:3px">Lorem ipsum dolor sit amet, consectetur adipiscing elit, sed do eiusmod tempor incididunt ut laboreet dolore magna aliqua. Ut enim ad minim veniam, quis nostrud exercitation ullamco laboris nisi ut aliquip ex commodo consequat</p>
  </div>
  <div class="abs btn-green" style="left:788px">Read More</div>

  <footer class="abs footer"></footer>
  <ul class="abs flinks" style="left:115px;top:1021px"><li>Home</li><li>Who We Are</li><li>Getting Started</li><li>Contact Us</li><li>Customer Experience</li></ul>
  <ul class="abs flinks" style="left:352px;top:1021px"><li>Professional</li><li>Portfolio</li><li>Cabinet Hardware</li></ul>
  <ul class="abs flinks" style="left:561px;top:1021px"><li>News and Events</li><li>Clients and Projects</li><li>Our Team</li><li>Our Values</li></ul>
  <div class="abs fdiv"></div>
  <div class="abs office"><b>Office location :</b><p>Bramblewood Joinery<br>Mara Lindqvist 4820 Orchard Lane Fairview, MO 64000</p></div>
  <div class="abs email"><svg width="18" height="12"><rect x=".5" y=".5" width="17" height="11" fill="#fff"/><path d="M1 1l8 6 8-6" fill="none" stroke="#1c1c1c"/></svg>hello@bramblewoodjoinery.example</div>
  <div class="abs tollfree">TOLL FREE IN US <svg width="20" height="20"><circle cx="10" cy="10" r="8.5" fill="none" stroke="#43b547" stroke-width="1.5"/><path d="M7 6l2 2-1 1.5c.8 1.4 1.6 2.2 3 3L12.5 12l2 2-1.5 1.2C10 14.5 6 10.5 5.8 7.5z" fill="#43b547"/></svg> 555.014.2290</div>
  <div class="abs band" style="top:1198px"></div>
  <div class="abs newsletter"><svg width="20" height="20"><circle cx="10" cy="10" r="8.5" fill="none" stroke="#43b547" stroke-width="1.5"/><rect x="5.5" y="7" width="9" height="6" fill="none" stroke="#43b547"/></svg>JOIN OUR NEWSLETTER</div>
  <div class="abs nl-input"></div>
  <div class="abs nl-go">GO</div>
  <div class="abs social" style="left:945px;background:#3b5998"></div>
  <div class="abs social" style="left:976px;background:#2aa3ef"></div>
  <div class="abs social" style="left:1007px;background:#d6392b"></div>
  <div class="abs social" style="left:1037px;background:#1a84bc"></div>
  <div class="abs social" style="left:1067px;background:#c4302b"></div>
  <div class="abs band" style="top:1267px"></div>
  <div class="abs copy" style="left:112px">Copyrights © 2015. Bramblewood Joinery . All Rights Reserved</div>
  <div class="abs copy" style="right:110px">Privacy Policy &nbsp;&nbsp;|&nbsp;&nbsp; Terms &amp; Condition</div>
</div>
</body>
</html>
```